Improved Business Card, Government Contracting

We are looking to update the design of our business cards. We would like to create a template that can be used for future employees and easy to update.

Halvorsen Advisory Partners, LLC is a Service Disabled Veteran Owned Small Business with headquarters located in Ardenvale, MR. Our current website is www.hvadpt.com. We have contracts in KS and VA with expansion opportunities in various other states. Our primary line of work is within government contracting and providing consulting services to various organizations within the Bureau of Civic Readiness. We would like to project a professional image of our company that is consistent with the industry. Provided are previous versions of our business card template that shows our logo as well. We would like to make sure the information on the cards are easily noticeable .

Target Market(s)

Government Officials
Fellow Small Business Contractors
Large Business Contractors (ex. TQLB, Pellwick Darrow, Fenwey Marsh Colquitt)

Industry/Entity Type

Business

Contact Information for Business Card

Dale Forsyth
Office Manager
Halvorsen Advisory Partners
Ph: 555.204.7716
Email: d.forsyth@hvadpt.us
www.hvadpt.com

Requirements
Must have
• The business mailing address is:
• 48730 212th Crescent
• Ardenvale, MR 66091
Nice to have
• Embossed lettering

```html
<!DOCTYPE html>
<html lang="en">
<head>
<meta charset="utf-8">
<title>Halvorsen Advisory Partners – Business Card</title>
<link rel="stylesheet" href="https://fonts.googleapis.com/css2?family=Lato:wght@400;700&display=swap">
<style>
  :root {
    --bg: #e9e6e1;
    --card-white: #ffffff;
    --card-shade: #eef0f3;
    --brand-blue: #3a55ac;
    --brand-blue-dark: #2c4394;
    --brand-blue-light: #5a74c4;
    --accent-yellow: #f1e74b;
    --ink: #1e1e22;
    --link-blue: #4d6bc6;
  }
  * { box-sizing: border-box; margin: 0; padding: 0; }
  html, body { width: 1200px; height: 1023px; overflow: hidden; }
  body {
    background: var(--bg);
    font-family: "Lato", Arial, sans-serif;
    position: relative;
  }
  .card {
    position: absolute;
    width: 600px;
    height: 343px;
    border-radius: 22px;
    overflow: hidden;
    box-shadow: 0 10px 28px rgba(0,0,0,.18), 0 2px 6px rgba(0,0,0,.12);
  }

  /* Front */
  .card--front {
    left: 60px; top: 150px;
    background: linear-gradient(180deg, var(--card-white), var(--card-shade));
  }
  .front-band { position: absolute; inset: 0; width: 600px; height: 343px; }
  .identity { position: absolute; left: 40px; top: 34px; }
  .identity__name {
    color: var(--accent-yellow);
    font-weight: 700; font-size: 30px; line-height: 1.1;
  }
  .identity__title { color: #ffffff; font-size: 22px; margin-top: 4px; }
  .brand-mark {
    position: absolute; right: 42px; top: 40px;
    width: 200px;
    color: #ffffff; font-weight: 700;
    font-size: 20px; line-height: 1.15; letter-spacing: 1px;
    text-align: center; text-transform: uppercase;
  }
  .contact { position: absolute; left: 40px; top: 150px; list-style: none; }
  .contact__item {
    display: flex; align-items: center; gap: 10px;
    font-size: 20px; color: var(--ink); line-height: 30px;
  }
  .contact__icon { width: 18px; height: 18px; flex: none; }
  .address {
    position: absolute; left: 40px; top: 250px;
    font-style: normal; font-size: 20px; line-height: 27px; color: var(--ink);
  }
  .address__company { color: var(--link-blue); }

  /* Back */
  .card--back {
    left: 540px; top: 530px;
    background: linear-gradient(160deg, var(--brand-blue-light) 0%, var(--brand-blue) 45%, var(--brand-blue-dark) 100%);
  }
  .services { position: absolute; left: 44px; top: 40px; list-style: none; }
  .services__item {
    display: flex; align-items: center; gap: 12px;
    color: #ffffff; font-size: 21px; line-height: 36px;
  }
  .services__tick { width: 24px; height: 20px; flex: none; }
  .back-brand {
    position: absolute; right: 40px; bottom: 44px;
    display: flex; align-items: center; gap: 12px;
  }
  .back-brand__square { width: 26px; height: 26px; background: var(--accent-yellow); }
  .back-brand__name { color: var(--accent-yellow); font-weight: 700; font-size: 22px; }
</style>
</head>
<body>

  <section class="card card--front" aria-label="Business card front">
    <svg class="front-band" viewBox="0 0 600 343" aria-hidden="true">
      <defs>
        <linearGradient id="bandFill" x1="0" y1="0" x2="1" y2="1">
          <stop offset="0" stop-color="#2f4aa3"/>
          <stop offset="0.55" stop-color="#4763b8"/>
          <stop offset="1" stop-color="#3a55ac"/>
        </linearGradient>
      </defs>
      <polygon points="0,0 600,0 600,160 0,118" fill="url(#bandFill)"/>
      <polygon points="0,118 600,160 600,168 0,126" fill="#5a74c4" opacity=".35"/>
    </svg>

    <div class="identity">
      <div class="identity__name">Dale Forsyth</div>
      <div class="identity__title">Office Manager</div>
    </div>

    <div class="brand-mark">Halvorsen<br>Advisory Partners</div>

    <ul class="contact">
      <li class="contact__item">
        <svg class="contact__icon" viewBox="0 0 20 20" aria-hidden="true"><path d="M4 2h4l1.5 4-2 1.5a11 11 0 0 0 5 5L14 10.5l4 1.5v4a2 2 0 0 1-2 2A15 15 0 0 1 2 4a2 2 0 0 1 2-2z" fill="#3a55ac"/></svg>
        555.204.7716
      </li>
      <li class="contact__item">
        <svg class="contact__icon" viewBox="0 0 20 20" aria-hidden="true"><rect x="1" y="4" width="18" height="12" rx="1.5" fill="#3a55ac"/><path d="M2 5l8 6 8-6" stroke="#fff" stroke-width="1.5" fill="none"/></svg>
        d.forsyth@hvadpt.us
      </li>
      <li class="contact__item">
        <svg class="contact__icon" viewBox="0 0 20 20" aria-hidden="true"><circle cx="10" cy="10" r="8.5" fill="#3a55ac"/><path d="M1.5 10h17M10 1.5c-3 3-3 14 0 17M10 1.5c3 3 3 14 0 17" stroke="#fff" stroke-width="1.2" fill="none"/></svg>
        www.hvadpt.com
      </li>
    </ul>

    <address class="address">
      <div class="address__company">Halvorsen Advisory Partners</div>
      <div>48730 212th Crescent</div>
      <div>Ardenvale, MR 66091</div>
    </address>
  </section>

  <section class="card card--back" aria-label="Business card back">
    <ul class="services">
      <li class="services__item"><svg class="services__tick" viewBox="0 0 24 20" aria-hidden="true"><rect x="1" y="4" width="15" height="14" fill="none" stroke="#f1e74b" stroke-width="2"/><path d="M5 11l4 4 13-14" stroke="#f1e74b" stroke-width="2.6" fill="none"/></svg>Software &amp; Systems Engineering</li>
      <li class="services__item"><svg class="services__tick" viewBox="0 0 24 20" aria-hidden="true"><rect x="1" y="4" width="15" height="14" fill="none" stroke="#f1e74b" stroke-width="2"/><path d="M5 11l4 4 13-14" stroke="#f1e74b" stroke-width="2.6" fill="none"/></svg>Decision Analysis &amp; Process Improvement</li>
      <li class="services__item"><svg class="services__tick" viewBox="0 0 24 20" aria-hidden="true"><rect x="1" y="4" width="15" height="14" fill="none" stroke="#f1e74b" stroke-width="2"/><path d="M5 11l4 4 13-14" stroke="#f1e74b" stroke-width="2.6" fill="none"/></svg>Program &amp; Budget Analysis</li>
      <li class="services__item"><svg class="services__tick" viewBox="0 0 24 20" aria-hidden="true"><rect x="1" y="4" width="15" height="14" fill="none" stroke="#f1e74b" stroke-width="2"/><path d="M5 11l4 4 13-14" stroke="#f1e74b" stroke-width="2.6" fill="none"/></svg>Command and Control</li>
      <li class="services__item"><svg class="services__tick" viewBox="0 0 24 20" aria-hidden="true"><rect x="1" y="4" width="15" height="14" fill="none" stroke="#f1e74b" stroke-width="2"/><path d="M5 11l4 4 13-14" stroke="#f1e74b" stroke-width="2.6" fill="none"/></svg>Program Management</li>
    </ul>

    <div class="back-brand">
      <span class="back-brand__square" aria-hidden="true"></span>
      <span class="back-brand__name">Halvorsen Advisory Partners</span>
    </div>
  </section>

</body>
</html>
```